Theme and starter template for small business powerpoint deck

We are starting a technology consulting company and would like to have a powerpoint/google slide theme and initial template. We are more concerned with the theme/colors at this point. Initial template can be pretty simple. We would want a cover slide, agenda slide, some content slides including text content, image content, a combination of both, etc. A closing slide. we have included jpg files of our logo, let us know if you would prefer eps/vector. I assume you may want exact color data as well?

Target Market(s)

Technology and Customer Experience Leadership at companies with 25 or more employees

Industry/Entity Type

Technology Consulting

Font styles to use
Sans Serif

Colors
0054AA
0677BA
7BADD7
CADEEF
E8F1F8

Requirements
Must have
• I have attached JPG and EPS and vector files to project. I would like to stay with those colors but open to slight variation if recommended.

```html
<!DOCTYPE html>
<html lang="en">
<head>
<meta charset="utf-8">
<title>Veltrana – Presentation Theme</title>
<link href="https://fonts.googleapis.com/css2?family=Poppins:wght@400;500;600;700&display=swap" rel="stylesheet">
<style>
  :root {
    --blue: #1259b3;
    --blue-deep: #0054aa;
    --blue-mid: #0677ba;
    --blue-soft: #7badd7;
    --blue-pale: #e8f1f8;
    --red: #cc3b3b;
    --grey: #a3a3a3;
    --title-grey: #9a9a9a;
    --ink: #1c1c1c;
    --body: #444;
    --page: #ffffff;
  }
  * { box-sizing: border-box; margin: 0; padding: 0; }
  html, body { width: 1002px; height: 1200px; overflow: hidden; background: var(--page); }
  body { position: relative; font-family: "Poppins", sans-serif; color: var(--ink); }

  .slide {
    position: absolute; width: 466px; height: 262px; overflow: hidden;
    background: #fff; box-shadow: 0 1px 4px rgba(0,0,0,.18);
  }
  .slide--blue { background: var(--blue); color: #fff; }
  .col-a { left: 25px; } .col-b { left: 511px; }
  .row-1 { top: 31px; } .row-2 { top: 321px; } .row-3 { top: 611px; } .row-4 { top: 899px; }

  .slide svg.art { position: absolute; inset: 0; width: 466px; height: 262px; }

  .heading-rule { position: absolute; left: 27px; top: 22px; width: 28px; height: 2px; background: var(--blue); }
  .heading { position: absolute; left: 27px; top: 28px; font-size: 12px; font-weight: 500; color: var(--title-grey); letter-spacing: .2px; }
  .heading b { color: var(--blue); font-weight: 600; }

  .footer-date { position: absolute; left: 17px; top: 234px; font-size: 7.5px; font-weight: 500; }
  .footer-brand { position: absolute; left: 195px; top: 230px; font-size: 11.5px; font-weight: 700; letter-spacing: .8px; color: var(--ink); }
  .page-no { position: absolute; left: 428px; top: 223px; width: 32px; height: 28px; }
  .page-no span { position: absolute; left: 0; width: 28px; top: 13px; text-align: center; font-size: 6px; font-weight: 600; color: #fff; }

  .copy { font-size: 6.6px; line-height: 17.5px; color: var(--body); }

  /* cover */
  .cover-brand { position: absolute; left: 24px; top: 46px; font-size: 31px; font-weight: 700; letter-spacing: 2px; }
  .cover-welcome { position: absolute; left: 24px; top: 109px; font-size: 15px; font-weight: 500; }
  .cover-tag { position: absolute; left: 24px; top: 145px; font-size: 8.6px; font-weight: 500; }
  .cover-intro { position: absolute; left: 24px; top: 166px; width: 180px; font-size: 6px; line-height: 14.5px; }

  /* agenda */
  .agenda-item { position: absolute; width: 110px; text-align: center; }
  .agenda-badge { width: 34px; height: 34px; margin: 0 auto; border-radius: 50%; background: var(--blue); color: #fff; font-size: 14px; font-weight: 600; line-height: 34px; }
  .agenda-label { margin-top: 9px; font-size: 6.5px; font-weight: 600; }

  /* what we do */
  .sub-title { position: absolute; top: 60px; font-size: 10px; font-weight: 600; color: var(--red); }
  .two-col { position: absolute; top: 78px; width: 205px; }

  /* services */
  .service { position: absolute; top: 102px; width: 82px; text-align: center; }
  .service h3 { font-size: 6.4px; font-weight: 600; color: var(--blue); margin-bottom: 5px; }
  .service p { font-size: 4.3px; line-height: 12.1px; color: var(--body); }

  /* timeline */
  .tl { position: absolute; width: 62px; text-align: center; font-size: 4.5px; line-height: 9px; color: var(--body); white-space: nowrap; }
  .tl b { display: block; font-weight: 500; color: var(--ink); margin-bottom: 1px; }
  .tl span { display: block; }

  /* closing */
  .close-brand { position: absolute; left: 261px; top: 34px; font-size: 28px; font-weight: 700; letter-spacing: 2px; }
  .close-thanks { position: absolute; left: 261px; top: 88px; font-size: 21px; font-weight: 500; }
  .contact { position: absolute; left: 295px; font-size: 6.6px; font-weight: 500; }
</style>
</head>
<body>

<!-- 01 Cover -->
<section class="slide slide--blue col-a row-1">
  <svg class="art" viewBox="0 0 466 262">
    <defs>
      <linearGradient id="coverPhoto" x1="0" y1="0" x2="1" y2="1">
        <stop offset="0" stop-color="#a9b8cc"/><stop offset=".55" stop-color="#dfe6ee"/><stop offset="1" stop-color="#6f8fb8"/>
      </linearGradient>
    </defs>
    <polygon points="332,21 458,240 206,240" fill="url(#coverPhoto)" role="img" aria-label="Photo of two colleagues reviewing work at a laptop in a bright office"/>
  </svg>
  <div class="cover-brand">VELTRANA</div>
  <div class="cover-welcome">WELCOME TO VELTRANA</div>
  <div class="cover-tag">A TECHNOLOGY CONSULTING COMPANY</div>
  <p class="cover-intro">Lorem ipsum dolor sit amet, consectetur adipiscing elit, sed do eiusmod tempor incididunt ut labore et dolore magna aliqua.</p>
</section>

<!-- 02 Agenda -->
<section class="slide col-b row-1">
  <div class="heading-rule"></div>
  <h2 class="heading">VELTRANA <b>SLIDE</b></h2>
  <div class="agenda-item" style="left:31px;top:72px"><div class="agenda-badge">1</div><div class="agenda-label">WELCOME SLIDE</div></div>
  <div class="agenda-item" style="left:138px;top:72px"><div class="agenda-badge">2</div><div class="agenda-label">VELTRANA SLIDE</div></div>
  <div class="agenda-item" style="left:245px;top:72px"><div class="agenda-badge">3</div><div class="agenda-label">WHAT WE DO</div></div>
  <div class="agenda-item" style="left:353px;top:72px"><div class="agenda-badge">4</div><div class="agenda-label">ABOUT VELTRANA</div></div>
  <div class="agenda-item" style="left:2px;top:159px"><div class="agenda-badge">5</div><div class="agenda-label">OUR SERVICES</div></div>
  <div class="agenda-item" style="left:109px;top:159px"><div class="agenda-badge">6</div><div class="agenda-label">OUR CHARTS</div></div>
  <div class="agenda-item" style="left:217px;top:159px"><div class="agenda-badge">7</div><div class="agenda-label">OUR TIMELINE</div></div>
  <div class="agenda-item" style="left:325px;top:159px"><div class="agenda-badge">8</div><div class="agenda-label">THANK YOU</div></div>
  <div class="footer-date">AUGUST 2024</div>
  <div class="footer-brand">VELTRANA</div>
  <div class="page-no"><svg width="32" height="28" viewBox="0 0 32 28"><polygon points="17,0 32,28 3,28" fill="var(--blue-soft)"/><polygon points="14,0 28,26 0,26" fill="var(--blue)"/></svg><span>02</span></div>
</section>

<!-- 03 What we do -->
<section class="slide col-a row-2">
  <div class="heading-rule"></div>
  <h2 class="heading">WHAT WE <b>DO</b></h2>
  <h3 class="sub-title" style="left:27px">OUR MISSION</h3>
  <p class="copy two-col" style="left:27px">Lorem ipsum dolor sit amet, consectetur adipiscing elit, sed do eiusmod tempor incididunt ut labore et dolore magna aliqua. Ut enim ad minim veniam, quis nostrud exercitation ullamco laboris nisi ut aliquip ex ea commodo consequat. Duis aute irure dolor in reprehenderit in voluptate velit esse cillum dolore eu fugiat nulla pariatur. Excepteur sint occaecat cupidatat non proident, sunt in culpa qui officia deserunt mollit anim id est laborum.</p>
  <h3 class="sub-title" style="left:249px">OUR VISION</h3>
  <p class="copy two-col" style="left:249px">Lorem ipsum dolor sit amet, consectetur adipiscing elit, sed do eiusmod tempor incididunt ut labore et dolore magna aliqua. Ut enim ad minim veniam, quis nostrud exercitation ullamco laboris nisi ut aliquip ex ea commodo consequat. Duis aute irure dolor in reprehenderit in voluptate velit esse cillum dolore eu fugiat nulla pariatur. Excepteur sint occaecat cupidatat non proident, sunt in culpa qui officia deserunt mollit anim id est laborum.</p>
  <div class="footer-date">AUGUST 2024</div>
  <div class="footer-brand">VELTRANA</div>
  <div class="page-no"><svg width="32" height="28" viewBox="0 0 32 28"><polygon points="17,0 32,28 3,28" fill="var(--blue-soft)"/><polygon points="14,0 28,26 0,26" fill="var(--blue)"/></svg><span>03</span></div>
</section>

<!-- 04 About -->
<section class="slide col-b row-2">
  <svg class="art" viewBox="0 0 466 262">
    <defs>
      <linearGradient id="aboutPhoto" x1="0" y1="0" x2="1" y2="1">
        <stop offset="0" stop-color="#c9cfd6"/><stop offset=".5" stop-color="#5d7486"/><stop offset="1" stop-color="#2c3c55"/>
      </linearGradient>
    </defs>
    <polygon points="115,60 203,213 27,213" fill="url(#aboutPhoto)" role="img" aria-label="Photo of two business people discussing at the office"/>
  </svg>
  <div class="heading-rule"></div>
  <h2 class="heading">ABOUT <b>VELTRANA</b></h2>
  <p class="copy" style="position:absolute;left:249px;top:32px;width:204px;">Lorem ipsum dolor sit amet, consectetur adipiscing elit, sed do eiusmod tempor incididunt ut labore et dolore magna aliqua. Ut enim ad minim veniam, quis nostrud exercitation ullamco laboris nisi ut aliquip ex ea commodo consequat. Duis aute irure dolor in reprehenderit in voluptate velit esse cillum dolore eu fugiat nulla pariatur. Excepteur sint occaecat cupidatat non proident, sunt in culpa qui officia deserunt mollit anim id est laborum. Lorem ipsum dolor sit amet, consectetur adipiscing elit, sed do eiusmod tempor incididunt ut labore et dolore magna aliqua.</p>
  <div class="footer-date">AUGUST 2024</div>
  <div class="footer-brand">VELTRANA</div>
  <div class="page-no"><svg width="32" height="28" viewBox="0 0 32 28"><polygon points="17,0 32,28 3,28" fill="var(--blue-soft)"/><polygon points="14,0 28,26 0,26" fill="var(--blue)"/></svg><span>04</span></div>
</section>

<!-- 05 Services -->
<section class="slide col-a row-3">
  <svg class="art" viewBox="0 0 466 262">
    <g id="chevrons">
      <g fill="var(--blue-deep)"><polygon points="13,66 91,66 97,76 91,86 13,86 19,76"/><polygon points="56,63 77,92 35,92"/></g>
      <g fill="var(--blue-mid)"><polygon points="102,66 180,66 186,76 180,86 102,86 108,76"/><polygon points="145,63 166,92 124,92"/></g>
      <g fill="var(--red)"><polygon points="191,66 269,66 275,76 269,86 191,86 197,76"/><polygon points="234,63 255,92 213,92"/></g>
      <g fill="var(--blue-mid)"><polygon points="280,66 358,66 364,76 358,86 280,86 286,76"/><polygon points="323,63 344,92 302,92"/></g>
      <g fill="var(--blue-deep)"><polygon points="369,66 447,66 453,76 447,86 369,86 375,76"/><polygon points="412,63 433,92 391,92"/></g>
    </g>
    <g fill="none" stroke="#fff" stroke-width=".9">
      <circle cx="56" cy="81" r="4"/><rect x="141" y="77" width="8" height="7"/>
      <circle cx="234" cy="80" r="4.5"/><circle cx="323" cy="81" r="4.5"/><circle cx="323" cy="81" r="2"/>
      <circle cx="412" cy="79" r="2.5"/><path d="M407 86h10"/>
    </g>
  </svg>
  <div class="heading-rule"></div>
  <h2 class="heading">OUR <b>SERVICES</b></h2>
  <div class="service" style="left:15px"><h3>LOREM IPSUM DOLOR</h3><p>Lorem ipsum dolor sit amet, consectetur adipiscing elit, sed do eiusmod tempor incididunt ut labore et dolore magna aliqua. Ut enim ad minim veniam, quis nostrud exercitation ullamco laboris nisi ut aliquip ex ea commodo consequat.</p></div>
  <div class="service" style="left:104px"><h3>LOREM IPSUM DOLOR</h3><p>Lorem ipsum dolor sit amet, consectetur adipiscing elit, sed do eiusmod tempor incididunt ut labore et dolore magna aliqua. Ut enim ad minim veniam, quis nostrud exercitation ullamco laboris nisi ut aliquip ex ea commodo consequat.</p></div>
  <div class="service" style="left:193px"><h3>LOREM IPSUM DOLOR</h3><p>Lorem ipsum dolor sit amet, consectetur adipiscing elit, sed do eiusmod tempor incididunt ut labore et dolore magna aliqua. Ut enim ad minim veniam, quis nostrud exercitation ullamco laboris nisi ut aliquip ex ea commodo consequat.</p></div>
  <div class="service" style="left:282px"><h3>LOREM IPSUM DOLOR</h3><p>Lorem ipsum dolor sit amet, consectetur adipiscing elit, sed do eiusmod tempor incididunt ut labore et dolore magna aliqua. Ut enim ad minim veniam, quis nostrud exercitation ullamco laboris nisi ut aliquip ex ea commodo consequat.</p></div>
  <div class="service" style="left:371px"><h3>LOREM IPSUM DOLOR</h3><p>Lorem ipsum dolor sit amet, consectetur adipiscing elit, sed do eiusmod tempor incididunt ut labore et dolore magna aliqua. Ut enim ad minim veniam, quis nostrud exercitation ullamco laboris nisi ut aliquip ex ea commodo consequat.</p></div>
  <div class="footer-date">AUGUST 2024</div>
  <div class="footer-brand">VELTRANA</div>
  <div class="page-no"><svg width="32" height="28" viewBox="0 0 32 28"><polygon points="17,0 32,28 3,28" fill="var(--blue-soft)"/><polygon points="14,0 28,26 0,26" fill="var(--blue)"/></svg><span>05</span></div>
</section>

<!-- 06 Chart -->
<section class="slide col-b row-3">
  <svg class="art" viewBox="0 0 466 262" font-family="Poppins, sans-serif">
    <g id="legend">
      <rect x="396" y="110" width="36" height="13" rx="6.5" fill="var(--blue-deep)"/>
      <rect x="396" y="127" width="36" height="13" rx="6.5" fill="var(--grey)"/>
      <rect x="396" y="144" width="36" height="13" rx="6.5" fill="var(--red)"/>
    </g>
    <g id="laptop">
      <rect x="203" y="66" width="205" height="131" rx="4" fill="#1d1d1d"/>
      <rect x="206" y="70" width="199" height="123" fill="#fff"/>
      <path d="M178 199h258l-4 6h-250z" fill="#b8b8b8"/>
    </g>
    <g id="chart" font-size="5.5" fill="var(--ink)">
      <g stroke="#d6d6d6" stroke-width=".5">
        <line x1="234" y1="85" x2="390" y2="85"/><line x1="234" y1="100" x2="390" y2="100"/>
        <line x1="234" y1="116" x2="390" y2="116"/><line x1="234" y1="131" x2="390" y2="131"/>
        <line x1="234" y1="146" x2="390" y2="146"/><line x1="234" y1="161" x2="390" y2="161"/>
        <line x1="234" y1="177" x2="390" y2="177"/>
      </g>
      <text x="223" y="87">6</text><text x="223" y="102">5</text><text x="223" y="118">4</text>
      <text x="223" y="133">3</text><text x="223" y="148">2</text><text x="223" y="163">1</text><text x="223" y="179">0</text>
      <rect x="242" y="112" width="3.5" height="65" fill="var(--blue-deep)"/>
      <rect x="250" y="141" width="3.5" height="36" fill="var(--grey)"/>
      <rect x="258" y="148" width="3.5" height="29" fill="var(--red)"/>
      <rect x="282" y="138" width="3.5" height="39" fill="var(--blue-deep)"/>
      <rect x="290" y="110" width="3.5" height="67" fill="var(--grey)"/>
      <rect x="298" y="148" width="3.5" height="29" fill="var(--red)"/>
      <rect x="321" y="125" width="3.5" height="52" fill="var(--blue-deep)"/>
      <rect x="329" y="151" width="3.5" height="26" fill="var(--grey)"/>
      <rect x="337" y="131" width="3.5" height="46" fill="var(--red)"/>
      <rect x="362" y="112" width="3.5" height="65" fill="var(--blue-deep)"/>
      <rect x="370" y="136" width="3.5" height="41" fill="var(--grey)"/>
      <rect x="378" y="100" width="3.5" height="77" fill="var(--red)"/>
      <g font-size="7.5"><text x="244" y="190">2021</text><text x="284" y="190">2022</text><text x="323" y="190">2023</text><text x="364" y="190">2024</text></g>
    </g>
  </svg>
  <div class="heading-rule" style="top:32px"></div>
  <h2 class="heading" style="top:38px">DATA DRIVEN <b>CHART</b></h2>
  <p class="copy" style="position:absolute;left:27px;top:65px;width:160px;">Lorem ipsum dolor sit amet, consectetur adipiscing elit, sed do eiusmod tempor incididunt ut labore et dolore magna aliqua. Ut enim ad minim veniam, quis nostrud exercitation ullamco laboris nisi ut aliquip ex ea commodo consequat.</p>
  <div class="footer-date">AUGUST 2024</div>
  <div class="footer-brand">VELTRANA</div>
  <div class="page-no"><svg width="32" height="28" viewBox="0 0 32 28"><polygon points="17,0 32,28 3,28" fill="var(--blue-soft)"/><polygon points="14,0 28,26 0,26" fill="var(--blue)"/></svg><span>06</span></div>
</section>

<!-- 07 Timeline -->
<section class="slide col-a row-4">
  <svg class="art" viewBox="0 0 466 262">
    <path d="M370 40 C370 58 360 66 346 66 H129 A30 30 0 0 0 129 126 H346 A30 30 0 0 1 346 186 H129 C112 186 102 194 98 204" fill="none" stroke="#222" stroke-width=".8"/>
    <g fill="#fff" stroke="#222" stroke-width=".9">
      <circle cx="99" cy="96" r="4"/><circle cx="374" cy="156" r="4"/>
      <circle cx="168" cy="66" r="4"/><circle cx="236" cy="66" r="4"/><circle cx="305" cy="66" r="4"/>
      <circle cx="168" cy="126" r="4"/><circle cx="236" cy="126" r="4"/><circle cx="305" cy="126" r="4"/>
      <circle cx="168" cy="186" r="4"/><circle cx="236" cy="186" r="4"/><circle cx="305" cy="186" r="4"/>
    </g>
    <g fill="var(--blue)">
      <circle cx="99" cy="96" r="2" fill="#222"/><circle cx="374" cy="156" r="2"/>
      <circle cx="168" cy="66" r="2"/><circle cx="236" cy="66" r="2" fill="#222"/><circle cx="305" cy="66" r="2"/>
      <circle cx="168" cy="126" r="2" fill="#222"/><circle cx="236" cy="126" r="2"/><circle cx="305" cy="126" r="2" fill="#222"/>
      <circle cx="168" cy="186" r="2" fill="#222"/><circle cx="236" cy="186" r="2"/><circle cx="305" cy="186" r="2" fill="#222"/>
    </g>
    <g id="goal" fill="none" stroke="#222" stroke-width=".9">
      <circle cx="373" cy="34" r="7"/><circle cx="373" cy="34" r="4"/><circle cx="373" cy="34" r="1.3" fill="#222"/>
      <path d="M374 33 L380 27 M378 26 l2 1 1 -2" stroke="var(--blue)"/>
    </g>
    <g id="start-arrow" fill="none" stroke="var(--blue)" stroke-width="1">
      <path d="M94 212 L104 200 M98 200 h6 v6"/>
    </g>
  </svg>
  <div class="heading-rule"></div>
  <h2 class="heading">OUR <b>TIMELINE</b></h2>
  <div class="tl" style="left:22px;top:84px"><b>2021</b><span>Sed ut perspiciatis</span><span>unde omnis iste natus</span></div>
  <div class="tl" style="left:137px;top:76px"><b>2022</b><span>Sed ut perspiciatis</span><span>unde omnis iste natus</span></div>
  <div class="tl" style="left:205px;top:76px"><b>2023</b><span>Sed ut perspiciatis</span><span>unde omnis iste natus</span></div>
  <div class="tl" style="left:274px;top:76px"><b>2024</b><span>Sed ut perspiciatis</span><span>unde omnis iste natus</span></div>
  <div class="tl" style="left:137px;top:134px"><b>2020</b><span>Sed ut perspiciatis</span><span>unde omnis iste natus</span></div>
  <div class="tl" style="left:205px;top:134px"><b>2019</b><span>Sed ut perspiciatis</span><span>unde omnis iste natus</span></div>
  <div class="tl" style="left:274px;top:134px"><b>2018</b><span>Sed ut perspiciatis</span><span>unde omnis iste natus</span></div>
  <div class="tl" style="left:380px;top:146px"><b>2017</b><span>Sed ut perspiciatis</span><span>unde omnis iste natus</span></div>
  <div class="tl" style="left:137px;top:196px"><b>2014</b><span>Sed ut perspiciatis</span><span>unde omnis iste natus</span></div>
  <div class="tl" style="left:205px;top:196px"><b>2015</b><span>Sed ut perspiciatis</span><span>unde omnis iste natus</span></div>
  <div class="tl" style="left:274px;top:196px"><b>2016</b></div>
  <div class="footer-date">AUGUST 2024</div>
  <div class="footer-brand">VELTRANA</div>
  <div class="page-no"><svg width="32" height="28" viewBox="0 0 32 28"><polygon points="17,0 32,28 3,28" fill="var(--blue-soft)"/><polygon points="14,0 28,26 0,26" fill="var(--blue)"/></svg><span>07</span></div>
</section>

<!-- 08 Closing -->
<section class="slide slide--blue col-b row-4">
  <svg class="art" viewBox="0 0 466 262">
    <defs>
      <linearGradient id="closePhoto" x1="0" y1="0" x2="1" y2="1">
        <stop offset="0" stop-color="#6c6560"/><stop offset=".5" stop-color="#c8b6a2"/><stop offset="1" stop-color="#4d4a4a"/>
      </linearGradient>
    </defs>
    <polygon points="146,21 272,238 20,238" fill="url(#closePhoto)" role="img" aria-label="Photo of smiling colleagues working together at a desk"/>
    <g id="contact-icons">
      <polygon points="273,122 285,144 261,144" fill="#fff"/>
      <polygon points="273,156 285,178 261,178" fill="#fff"/>
      <polygon points="273,190 285,212 261,212" fill="#fff"/>
      <path d="M270 134 q0 6 6 6 l1 -1.5 -2 -1.5 -1 1 q-2 -1 -2.5 -2.5 l1 -1 -1.5 -2z" fill="var(--blue)"/>
      <rect x="270" y="169" width="6" height="4" fill="none" stroke="var(--blue)" stroke-width=".7"/>
      <path d="M270 169 l3 2.3 3 -2.3" fill="none" stroke="var(--blue)" stroke-width=".7"/>
      <path d="M273 208 c-2.5 -3 -3 -4 -3 -5 a3 3 0 0 1 6 0 c0 1 -.5 2 -3 5z" fill="none" stroke="var(--blue)" stroke-width=".8"/>
    </g>
  </svg>
  <div class="close-brand">VELTRANA</div>
  <div class="close-thanks">THANK YOU</div>
  <div class="contact" style="top:135px">+1 555 010 0100</div>
  <div class="contact" style="top:169px">HELLO@VELTRANA.EXAMPLE</div>
  <div class="contact" style="top:203px">56, VELTRANA LOREM LIPSUM 908 782</div>
</section>

</body>
</html>
```